Business Card Design Project

We are not a new company, but renamed to "Vantorin Kitchens" last year. We specialize in modern high-end cabinetry imports. We would like to communicate a sense of quality and cutting edge technology. Ideally the design would incorporate our logo colors, silver, red and preferably a black, matte background. Though we are open to suggestions.
Logo is attached.
Edit: I have attached rough drafts of the previous cards, this way you will have all necessary content that needs to go on the cards.
Updates
Project Deadline Extended
Reason: We have received a lot of great designs, but due to the sheer number we couldn't respond to all. We will extend the deadline for another 7 days to finalize and provide feedback to designers.
Thank you for your hard work!
Industry/Entity Type
Business
Look and feel
Each slider illustrates characteristics of the customer's brand and the style your logo design should communicate.

```html
<!DOCTYPE html>
<html lang="en">
<head>
<meta charset="utf-8">
<title>Vantorin Kitchens – Business Cards</title>
<link href="https://fonts.googleapis.com/css2?family=Arimo:wght@400;700&family=Michroma&family=Source+Sans+3:wght@400&display=swap" rel="stylesheet">
<style>
  :root {
    --sheet: #d9d1c7;
    --label: #1a1a1a;
    --card-dark: #141415;
    --card-mid: #2b2c2e;
    --silver: #c9cacc;
    --silver-light: #eeeff0;
    --silver-dark: #8e8f92;
    --red: #e31e24;
    --text: #ffffff;
    --text-soft: #e4e4e4;
    --icon: #a7a8aa;
  }
  * { margin: 0; padding: 0; box-sizing: border-box; }
  html, body { width: 1200px; height: 788px; overflow: hidden; }
  body { background: var(--sheet); position: relative; font-family: "Arimo", Arial, sans-serif; }

  .label {
    position: absolute;
    font-family: "Source Sans 3", "Myriad Pro", sans-serif;
    font-size: 21px;
    color: var(--label);
    transform: translateX(-50%);
  }

  .card {
    position: absolute;
    width: 525px;
    height: 299px;
    border-radius: 18px;
    overflow: hidden;
    background:
      radial-gradient(ellipse at 40% 30%, var(--card-mid) 0%, var(--card-dark) 85%);
    box-shadow: 0 4px 10px rgba(0,0,0,.35);
  }

  .brand-name {
    position: absolute;
    font-family: "Michroma", "Arimo", sans-serif;
    color: var(--silver);
    letter-spacing: 1px;
    white-space: nowrap;
  }

  .card-front .brand-name { left: 33px; top: 84px; font-size: 20px; }
  .brand-mark {
    position: absolute;
    background: var(--red);
  }
  .card-front .brand-mark { left: 33px; top: 52px; width: 22px; height: 22px; }

  .edge-stripe { position: absolute; right: 0; top: 0; width: 32px; height: 299px; }

  .person { position: absolute; left: 33px; top: 133px; color: var(--text); }
  .person-name { font-weight: 700; font-size: 18px; letter-spacing: .3px; }
  .person-role { font-size: 13px; margin-top: 2px; color: var(--text-soft); }

  .contact-list { position: absolute; left: 33px; top: 181px; list-style: none; }
  .contact-list li {
    display: flex; align-items: center;
    height: 19.5px;
    font-size: 13px; color: var(--text-soft);
  }
  .contact-list svg { width: 12px; height: 12px; margin-right: 18px; fill: var(--icon); flex: none; }

  .card-back .brand-name { left: 0; right: 0; text-align: center; top: 160px; font-size: 24px; }
  .card-back .brand-mark { left: 251px; top: 100px; width: 24px; height: 24px; }

  .card-back-alt { background: linear-gradient(160deg, #1b1b1c, #0c0c0c 60%, #151515); }
  .card-back-alt .brand-name { top: 173px; }
  .card-back-alt .brand-mark { top: 110px; }
  .texture-zone { position: absolute; }
  .texture-top {
    left: 0; top: 0; width: 300px; height: 95px;
    background: radial-gradient(ellipse at 45% 30%, rgba(120,120,125,.55), rgba(40,40,42,0) 70%);
  }
  .texture-bottom {
    right: 0; bottom: 0; width: 250px; height: 95px;
    background: radial-gradient(ellipse at 50% 60%, rgba(120,120,125,.55), rgba(40,40,42,0) 70%);
  }
</style>
</head>
<body>

  <svg width="0" height="0" style="position:absolute" aria-hidden="true">
    <defs>
      <linearGradient id="silverFade" x1="0" y1="0" x2="1" y2="0">
        <stop offset="0" stop-color="#8e8f92"/>
        <stop offset=".5" stop-color="#eeeff0"/>
        <stop offset="1" stop-color="#b9babc"/>
      </linearGradient>
      <symbol id="icon-phone" viewBox="0 0 12 12"><path d="M3 1l2 2.5-1.2 1.2c.6 1.3 1.5 2.2 2.8 2.8L7.8 6.3 10.5 8.3 9.3 10.8C5 10.5 1.5 7 1.2 2.7z"/></symbol>
      <symbol id="icon-fax" viewBox="0 0 12 12"><path d="M3 1h6v3H3zM1 5h10v4H9v2H3V9H1zM4 8v2h4V8z"/></symbol>
      <symbol id="icon-mobile" viewBox="0 0 12 12"><path d="M3.5 0h5a1 1 0 0 1 1 1v10a1 1 0 0 1-1 1h-5a1 1 0 0 1-1-1V1a1 1 0 0 1 1-1zM4 2v6h4V2z"/></symbol>
      <symbol id="icon-mail" viewBox="0 0 12 12"><path d="M0 3h12v7H0zM1 4l5 3.5L11 4z"/></symbol>
      <symbol id="icon-home" viewBox="0 0 12 12"><path d="M6 1l6 5h-2v5H7.5V8h-3v3H2V6H0z"/></symbol>
    </defs>
  </svg>

  <span class="label" style="left:307px; top:22px;">front</span>
  <span class="label" style="left:889px; top:22px;">front-1</span>
  <span class="label" style="left:314px; top:405px;">back</span>
  <span class="label" style="left:879px; top:405px;">Back - 1</span>

  <!-- Front: President -->
  <article class="card card-front" style="left:50px; top:63px;">
    <span class="brand-mark"></span>
    <span class="brand-name">VANTORIN KITCHENS</span>
    <svg class="edge-stripe" viewBox="0 0 32 299" aria-hidden="true">
      <polygon points="0,0 32,0 32,88 0,118" fill="var(--red)"/>
      <polygon points="0,118 32,88 32,299 0,299" fill="url(#silverFade)"/>
    </svg>
    <div class="person">
      <p class="person-name">MIREK DALTON</p>
      <p class="person-role">President</p>
    </div>
    <ul class="contact-list">
      <li><svg><use href="#icon-phone"/></svg>555.210.0417</li>
      <li><svg><use href="#icon-fax"/></svg>555.210.0482</li>
      <li><svg><use href="#icon-mobile"/></svg>555.308.1926</li>
      <li><svg><use href="#icon-mail"/></svg>mirek@vantorinkitchens.ca</li>
      <li><svg><use href="#icon-home"/></svg>1820 - 42 Ave., Calgary, AB T2B 3K9</li>
    </ul>
  </article>

  <!-- Front: Director -->
  <article class="card card-front" style="left:626px; top:63px;">
    <span class="brand-mark"></span>
    <span class="brand-name">VANTORIN KITCHENS</span>
    <svg class="edge-stripe" viewBox="0 0 32 299" aria-hidden="true">
      <polygon points="0,0 32,0 32,88 0,118" fill="var(--red)"/>
      <polygon points="0,118 32,88 32,299 0,299" fill="url(#silverFade)"/>
    </svg>
    <div class="person">
      <p class="person-name">OSKAR DALTON</p>
      <p class="person-role">Director</p>
    </div>
    <ul class="contact-list">
      <li><svg><use href="#icon-phone"/></svg>555.210.0417</li>
      <li><svg><use href="#icon-fax"/></svg>555.210.0482</li>
      <li><svg><use href="#icon-mobile"/></svg>555.614.2750</li>
      <li><svg><use href="#icon-mail"/></svg>oskar@vantorinkitchens.ca</li>
      <li><svg><use href="#icon-home"/></svg>1820 - 42 Ave., Calgary, AB T2B 3K9</li>
    </ul>
  </article>

  <!-- Back -->
  <article class="card card-back" style="left:56px; top:447px;">
    <span class="brand-mark"></span>
    <span class="brand-name">VANTORIN KITCHENS</span>
  </article>

  <!-- Back alternative -->
  <article class="card card-back card-back-alt" style="left:625px; top:446px;">
    <div class="texture-zone texture-top" role="img" aria-label="Perforated metal texture, upper left corner"></div>
    <div class="texture-zone texture-bottom" role="img" aria-label="Perforated metal texture, lower right corner"></div>
    <span class="brand-mark"></span>
    <span class="brand-name">VANTORIN KITCHENS</span>
  </article>

</body>
</html>
```